Book for new dads needs a cover.

We need a cover for a book titled Roadmap to Early Parenthood: Practical Methods for Welcoming a Newborn, Juggling Career and Home Life, and Managing Mental Health on the Path to Becoming a Parent. We would like to see a design that emphasizes healthy babies and confident dads.

```html
<!DOCTYPE html>
<html lang="en">
<head>
<meta charset="UTF-8">
<title>Roadmap to Early Parenthood — Book Cover</title>
<link rel="stylesheet" href="https://fonts.googleapis.com/css2?family=Exo+2:wght@500;600&family=Roboto+Condensed:ital,wght@0,700;1,700&display=swap">
<style>
  :root {
    --stage: #d9d9dc;
    --olive: #676b4a;
    --olive-dark: #55593c;
    --orange: #f28a3c;
    --orange-deep: #e2742a;
    --band-orange: #c9742f;
    --charcoal: #3b3c35;
    --glow: #ffd27a;
    --white: #ffffff;
    --ink: #3a2a1c;
  }
  * { margin: 0; padding: 0; box-sizing: border-box; }
  html, body { width: 1200px; height: 870px; overflow: hidden; background: var(--stage); }
  .canvas { position: relative; width: 1200px; height: 870px; }

  .cover {
    position: absolute; left: 310px; top: 35px; width: 580px; height: 800px;
    background: var(--olive); overflow: hidden;
    box-shadow: 0 10px 30px rgba(0,0,0,.25);
  }
  .cover__band--olive { position: absolute; inset: 0 0 auto 0; height: 300px;
    background: linear-gradient(180deg, var(--olive-dark), var(--olive)); }
  .cover__photo {
    position: absolute; left: 0; top: 300px; width: 580px; height: 410px;
    background:
      radial-gradient(ellipse 220px 180px at 170px 210px, rgba(255,230,160,.95), rgba(255,180,70,.55) 45%, rgba(0,0,0,0) 75%),
      linear-gradient(180deg, var(--band-orange) 0 120px, var(--charcoal) 120px 100%);
  }
  .cover__photo-shade {
    position: absolute; left: 0; top: 300px; width: 580px; height: 410px;
    background: linear-gradient(90deg, rgba(0,0,0,0) 55%, rgba(40,40,34,.35));
  }
  .cover__band--bottom { position: absolute; left: 0; bottom: 0; width: 580px; height: 90px;
    background: linear-gradient(180deg, var(--orange-deep), var(--orange)); }

  .title { position: absolute; left: 0; top: 70px; width: 580px; text-align: center;
    font-family: "Exo 2", sans-serif; font-weight: 600; line-height: .95; }
  .title__lead { display: block; color: var(--orange); font-size: 56px; letter-spacing: 1px; }
  .title__main { display: block; color: var(--orange); font-size: 150px; margin-top: 4px; }
  .title__tail { display: block; color: var(--white); font-size: 66px; margin-top: 30px; letter-spacing: 1px; }

  .ribbon { position: absolute; left: 50%; top: 440px; transform: translateX(-50%); }
  .ribbon__label { position: absolute; inset: 0; display: flex; align-items: center; justify-content: center;
    font-family: "Roboto Condensed", sans-serif; font-weight: 700; font-size: 30px; color: var(--ink); letter-spacing: 1px; }

  .summary { position: absolute; left: 40px; top: 515px; width: 500px; text-align: center;
    font-family: "Roboto Condensed", sans-serif; font-weight: 700; font-style: italic;
    color: var(--white); font-size: 21px; line-height: 1.3; text-transform: uppercase; }

  .tagline { position: absolute; left: 0; bottom: 14px; width: 580px; text-align: center;
    font-family: "Roboto Condensed", sans-serif; font-weight: 700; font-style: italic;
    color: var(--white); font-size: 22px; line-height: 1.25; text-transform: uppercase; }
</style>
</head>
<body>
<div class="canvas">
  <article class="cover">
    <div class="cover__band--olive"></div>
    <div class="cover__photo" role="img" aria-label="Sunset photograph of a father holding his baby in silhouette against warm golden light"></div>
    <div class="cover__photo-shade"></div>
    <div class="cover__band--bottom"></div>

    <h1 class="title">
      <span class="title__lead">ROADMAP TO</span>
      <span class="title__main">EARLY</span>
      <span class="title__tail">PARENTHOOD</span>
    </h1>

    <div class="ribbon">
      <svg width="380" height="58" viewBox="0 0 380 58" aria-hidden="true">
        <polygon points="0,8 36,8 36,54 0,54 14,31" fill="var(--orange-deep)"/>
        <polygon points="380,8 344,8 344,54 380,54 366,31" fill="var(--orange-deep)"/>
        <rect x="26" y="2" width="328" height="48" fill="var(--orange)"/>
      </svg>
      <span class="ribbon__label">EASY HAND BOOK</span>
    </div>

    <p class="summary">
      Simple guide to help caring dads take care<br>
      of their pregnant partner and bond with their<br>
      unborn child for the<br>
      upcoming 9 months.
    </p>

    <p class="tagline">How to prepare for fatherhood<br>with complete confidence</p>
  </article>
</div>
</body>
</html>
```